Systems and Technology Consultants - Website

Design & Build a website for a new company which operates in the Systems and Technology space for Transportation, Government and Commercial sectors.

Overall design should be minimalist in nature.
Should also have a feed that provides news and event updates on the main page.
Logo has already been awarded and should be incorporated into the site.

We like the overall layout, functionality and simplicity of the below sites. Submitted designs could be similar to or a combination of the aspects on these sites, or perhaps a whole different concept - we are open to new ideas.
Norvique.com
Teblo.it

Update 1 Dated 27 May 2014

All I am moving away from the Teblo.it website and would like it to be more aligned with Norvique.com not only in layout but in functionality. I will be extending the deadline of this design brief for two weeks to incorporate additional requirements and will add addtional funding to the project.

Apologies for not having more information available to provide but with so many submissions its getting confusing.

Thanks Derek

Please note that the brief has been updated and the deadline has been extended.

Important: We will need two language versions of the website, English and Arabic; the website is hosted on HostPelican

Hello All, Thank you for your submissions. We have narrowed it down to the final 6 designers and I just wanted to take a moment and provide a bit of feedback regarding the concepts that we like and the modifications we are looking for. First, let me mention some of the design functions we like. - At the top of the homepage we really like the "region" or "language" tab so that the website can be viewed in both English and Arabic. - We like the homepage to have clear color variation so that the different sections of the homepage are distinct. Additionally, we like the bottom portion of the homepage to be in red. We feel that draws attention to our contact information. Again, we would like the colors to integrate black, gray-scale, red, etc. - Having a search tab at the top of the home page, or integrated into the main image, so that the site is easy to navigate. - We especially like the main image to have the scrolling tabs at the bottom so it is easy to browse the services offered (Consultancy, Solutions Architecture, Masters Systems Integration, Independent Design Review). - In regards to the services offered tab we really like the idea that a few people presented that have the outside of our logo with an icon in the middle of consultancy, solutions, etc., etc. Secondly, as mentioned in our brief we really enjoy the design of norvique site. Specially, we enjoy the strong iconic images they use, the way the tabs at the top scroll easily, and contact us page that generates an email. Lastly, I've included some photos of the concept we have been working on. What we are trying to demonstrate is how our company offers a range of services that are essentially linked together. We provide individual services that when combined present the full service package. We would like this concept to be integrated into the over concept of our website. Please feel free to ask for clarification of any of the above points or contact us if you have any additional questions. We appreciate all of your hard work and are very excited to see the updated designs. Best, Marta Vennick Quelbrant Senior Program Manager marta.vennick@quelbrant-example.com

Industry/Entity Type

Government

Font styles to use
Serif
Sans Serif

Requirements
Must have
• Must work on/adapt to various/mobile devices (responsive)
Must be simple and straightforward
Colors should be in line/matching with logo
2 language versions: English and Arabic (no Thai)
Services should be the first group/row of items after/below the main image
Note: the website will be hosted by hostpelican
Nice to have
• Submit feedback form
What's New section
The banner at the bottom of the site should not be too large; we would like a narrow one more
It would be nice if the header/top banner (with Home, About, etc. tabs) could stay in place as you scroll down (like Norvique and Chatterloop)
We will likely only use one image with a Company slogan on the Home page rather than a carousel of images to rotate through
Should not have
• This is the existing website: http://www.quelbrant-example.org
We do not like the animation, the way the banner icons/titles bounce
Not simple enough, we don't like the functionality or how pages load so slowly
We do not like the logo centered - it should be at the left
The banner and its tabs should not be towards the right, we would like them to be centered, to go all the way across and to be below the logo

```html
<!DOCTYPE html>
<html lang="en">
<head>
<meta charset="utf-8">
<title>Quelbrant International</title>
<link rel="stylesheet" href="https://fonts.googleapis.com/css2?family=Ubuntu:wght@300;400;500;700&display=swap">
<style>
:root{
  --red:#e0202a;
  --red-deep:#a8141c;
  --ink:#555;
  --muted:#9a9a9a;
  --line:#e3e3e3;
  --dark:#333333;
  --darker:#2a2a2a;
  --white:#fff;
  --foot-text:#a9a9a9;
}
*{margin:0;padding:0;box-sizing:border-box}
html,body{width:1200px;height:1200px;overflow:hidden}
body{font-family:"Ubuntu",sans-serif;color:var(--ink);background:var(--white);position:relative}

/* header */
.site-header{position:absolute;left:0;top:0;width:1200px;height:48px;background:var(--white);border-bottom:2px solid var(--red)}
.brand{position:absolute;left:186px;top:13px;display:flex;align-items:center;gap:8px}
.brand-dot{width:20px;height:20px;border:3px solid var(--red);border-radius:50%}
.brand-name{color:var(--red);font-weight:700;font-size:13px;letter-spacing:3px;line-height:11px}
.brand-name small{display:block;font-size:7px;letter-spacing:2.6px;margin-top:2px}
.main-nav{position:absolute;top:18px;left:0;width:950px;height:16px;font-size:13px;color:var(--muted)}
.main-nav span{position:absolute;top:0;white-space:nowrap}
.main-nav .active{color:var(--red)}
.caret{display:inline-block;border:4px solid transparent;border-top-color:var(--muted);margin-left:3px;vertical-align:-1px}
.social-top{position:absolute;top:16px;left:952px;display:flex;gap:7px}
.social-top i{width:18px;height:18px;border-radius:50%;background:#ccc}
.social-top i.on{background:var(--red)}

/* hero */
.hero{position:absolute;left:0;top:48px;width:1200px;height:370px;background:radial-gradient(circle at 720px 190px,#e9303a 0,#c21c25 35%,#9e1118 80%)}
.hero-visual{position:absolute;left:150px;top:0;width:450px;height:370px;background:linear-gradient(160deg,#2b2b2e 0%,#55545a 45%,#c9b9bf 75%,#9e1118 100%);opacity:.9}
.hero-band{position:absolute;left:600px;top:130px;width:600px;height:110px;background:linear-gradient(90deg,rgba(255,255,255,.06),rgba(255,255,255,.14),rgba(255,255,255,.04))}
.hero-badge{position:absolute;left:658px;top:122px;width:128px;height:128px;border-radius:50%;background:var(--white);box-shadow:0 0 0 8px rgba(255,255,255,.18)}
.hero-name{position:absolute;left:802px;top:164px;width:210px;color:var(--white);font-weight:700;font-size:27px;letter-spacing:4px;line-height:30px}
.hero-name small{display:block;font-size:12px;letter-spacing:4.4px;margin:8px 0 0 22px;line-height:14px}
.hero-tagline{position:absolute;right:191px;top:288px;width:520px;text-align:right;color:var(--white);font-size:16px;line-height:19px}

/* intro */
.section-title{color:var(--red);font-size:24px;font-weight:400}
.welcome{position:absolute;left:197px;top:459px;width:375px}
.welcome p{font-size:12.5px;line-height:14.6px;margin-top:14px;color:#666}
.welcome .section-title+p{margin-top:7px}
.divider{position:absolute;left:598px;top:497px;width:1px;height:268px;background:var(--line)}
.services{position:absolute;left:621px;top:459px}
.tile{position:absolute;width:127px;height:121px;border:1px solid var(--line);background:var(--white);text-align:center;font-size:12px;color:#aaa;padding-top:30px}
.tile svg{display:block;margin:0 auto 10px}
.tile.on{background:var(--red);border-color:var(--red);color:var(--white);font-weight:500}

/* footer */
.site-footer{position:absolute;left:0;top:828px;width:1200px;height:310px;background:var(--dark);color:var(--white)}
.col{position:absolute;top:40px;width:237px}
.col h3{font-weight:400;font-size:14.5px;height:27px;border-bottom:1px solid #4a4a4a}
.col-icon{position:absolute;right:2px;top:2px;width:16px;height:14px;border:2px solid #ddd;border-radius:2px}
.item{position:relative;border-bottom:1px solid #4a4a4a;padding:13px 0 8px;font-size:11px;line-height:12.4px;color:var(--foot-text)}
.item b{color:var(--white);font-weight:500;display:block;font-size:11px}
.thumb{float:left;width:55px;height:46px;margin:0 7px 4px 0;background:linear-gradient(#cfd6dc,#8f8a86)}
.thumb.logo{background:var(--white);display:flex;align-items:center;justify-content:center}
.thumb.logo span{width:22px;height:22px;border:3px solid var(--red);border-radius:50%}
.more{display:block;text-align:right;margin-top:4px;color:var(--white)}
.more.red{color:var(--red)}
.date{position:absolute;right:0;top:13px;color:var(--white);font-weight:500;letter-spacing:1px}
.foot-brand{margin-top:10px;display:flex;align-items:center;gap:8px;color:var(--white);font-weight:700;font-size:14px;letter-spacing:3.6px;line-height:12px}
.foot-brand i{width:20px;height:20px;border:3px solid var(--white);border-radius:50%}
.foot-brand small{display:block;font-size:7px;letter-spacing:2.5px;margin:3px 0 0 14px}
.contact-text{font-size:11px;line-height:12.4px;color:var(--foot-text);margin-top:10px}
.contact-text b{color:var(--white);font-weight:500;display:block;margin-bottom:3px}
.social-foot{display:flex;gap:7px;margin-top:10px}
.social-foot i{width:18px;height:18px;border-radius:50%;background:#666}
.social-foot i.on{background:var(--red)}
.bottom-bar{position:absolute;left:0;top:1138px;width:1200px;height:62px;background:var(--darker);font-size:10px;color:var(--foot-text)}
.bottom-bar p{position:absolute;left:192px;top:25px}
.share{position:absolute;left:940px;top:23px;display:flex;gap:4px}
.share i{width:28px;height:17px;background:var(--red);border-radius:2px}
.share span{width:36px;height:17px;background:var(--white);border-radius:2px;color:#555;font-size:9px;text-align:center;line-height:17px}
</style>
</head>
<body>

<header class="site-header">
  <div class="brand"><span class="brand-dot"></span><div class="brand-name">QUELBRANT<small>INTERNATIONAL</small></div></div>
  <nav class="main-nav">
    <span class="active" style="left:452px">Home</span>
    <span style="left:518px">Business Unit</span>
    <span style="left:623px">Services<i class="caret"></i></span>
    <span style="left:706px">About Us</span>
    <span style="left:788px">Locations</span>
    <span style="left:872px">Contact Us</span>
  </nav>
  <div class="social-top"><i class="on"></i><i></i><i></i></div>
</header>

<section class="hero">
  <div class="hero-band"></div>
  <div class="hero-visual" role="img" aria-label="Photo of a businessman holding a glowing globe with connected devices and people icons"></div>
  <div class="hero-badge"></div>
  <div class="hero-name">QUELBRANT<small>INTERNATIONAL</small></div>
  <p class="hero-tagline">Quelbrant Int. specializes in delivering quality professional services and<br>technical projects that support larger business goals.</p>
</section>

<section class="welcome">
  <h2 class="section-title">Welcome</h2>
  <p>Quelbrant specializes in delivering quality professional services and technical projects that support larger business goals. systems are tools that support a greater business function and need. we understand that most technical projects are conceptualized to support a larger vision with actual business goals in mind and ensure that all of our professional and certified expertise is included in our professional services to meet those goals.</p>
  <p>quelbrant recognizes the middle east and greater asia regions are economic growth markets with developing infrastructure projects requiring specialist systems and technical expertise. accordingly, quelbrant has evolved its presence in the regions to meet client demands and expectations.</p>
  <p>our ultimate goal is to provide quality, technical and professional services on projects of any scale and/or complexity, from conception through to completion. our philosophy is simple; stick to what you are good at and be the best at it.</p>
</section>
<div class="divider"></div>

<section class="services">
  <h2 class="section-title">Services</h2>
  <div class="tile" style="left:0;top:38px">
    <svg width="36" height="34" viewBox="0 0 36 34" fill="#b5b5b5"><circle cx="8" cy="5" r="4"/><circle cx="18" cy="5" r="4"/><circle cx="28" cy="5" r="4"/><rect x="4" y="12" width="28" height="5"/><rect x="6" y="18" width="4" height="14"/><rect x="26" y="18" width="4" height="14"/><rect x="15" y="18" width="6" height="10"/></svg>CONSULTING</div>
  <div class="tile on" style="left:131px;top:38px">
    <svg width="44" height="36" viewBox="0 0 44 36" fill="#fff"><rect x="16" y="0" width="12" height="6"/><rect x="8" y="8" width="12" height="6"/><rect x="24" y="8" width="12" height="6"/><rect x="2" y="16" width="40" height="6"/><rect x="2" y="24" width="18" height="10"/><path d="M24 34 L33 22 L42 34Z"/></svg>ENGINEERING</div>
  <div class="tile" style="left:262px;top:38px">
    <svg width="44" height="40" viewBox="0 0 44 40" fill="#b5b5b5"><circle cx="16" cy="26" r="11"/><circle cx="34" cy="10" r="8"/><circle cx="16" cy="26" r="4" fill="#fff"/><circle cx="34" cy="10" r="3" fill="#fff"/></svg>MAINTENANCE</div>
  <div class="tile" style="left:0;top:166px">
    <svg width="38" height="36" viewBox="0 0 38 36" fill="#b5b5b5"><circle cx="6" cy="6" r="4"/><rect x="2" y="12" width="8" height="22"/><rect x="12" y="4" width="24" height="20" fill="none" stroke="#b5b5b5" stroke-width="3"/><path d="M20 34 L24 26 L28 34" fill="none" stroke="#b5b5b5" stroke-width="2"/></svg>OPERATIONS</div>
  <div class="tile" style="left:131px;top:166px">
    <svg width="44" height="34" viewBox="0 0 44 34" fill="#b5b5b5"><rect x="10" y="2" width="12" height="6"/><rect x="24" y="2" width="12" height="6"/><rect x="2" y="10" width="18" height="6"/><rect x="22" y="10" width="20" height="6"/><rect x="10" y="18" width="24" height="6"/><rect x="2" y="26" width="18" height="6"/><rect x="22" y="26" width="20" height="6"/></svg>CONSTRUCTION</div>
</section>

<footer class="site-footer">
  <div class="col" style="left:196px">
    <h3>Latest News</h3><span class="col-icon"></span>
    <div class="item"><span class="thumb" role="img" aria-label="News photo of a runner on a track"></span><b>Lorem ipsum</b>Lorem ipsum dolor sit amet, consectetuer adipiscing elit, sed diam nonummy nibh euismod tincidunt ut laoreet dolore magna aliquam erat volutpat.<span class="more red">Read More...</span></div>
    <div class="item"><span class="thumb logo"><span></span></span><b>Duis autem vel</b>Ut wisi enim ad minim veniam, quis nostrud exerci tation ullamcorper suscipit lobortis nisl ut aliquip ex ea commodo consequat.<span class="more">Read More...</span></div>
  </div>
  <div class="col" style="left:485px">
    <h3>Events</h3><span class="col-icon"></span>
    <div class="item"><b>Lorem ipsum</b><span class="date">11-22-2014</span>Ut wisi enim ad minim veniam, quis nostrud exerci tation ullamcorper suscipit lobortis nisl ut aliquip ex ea commodo consequat.<br><br><span class="more">Go to Event&nbsp;</span></div>
    <div class="item"><b>Lorem ipsum</b><span class="date">11-22-2014</span>Duis autem vel eum iriure dolor in hendrerit in vulputate velit esse molestie consequat, vel illum dolore eu feugiat nulla facilisis at vero eros et accumsan ...<span class="more">Go to Event&nbsp;</span></div>
  </div>
  <div class="col" style="left:771px">
    <h3>Contact Us</h3><span class="col-icon"></span>
    <div class="foot-brand"><i></i><div>QUELBRANT<small>INTERNATIONAL</small></div></div>
    <div class="contact-text"><b>Main Office Bangkok Branch</b>address: 14 linden grove rd, harrow court, eastfield, bangkok 10990<br>phone numbers: +(66)-02-555-0147-8<br>email: info@quelbrant-example.org</div>
    <div class="social-foot"><i></i><i></i><i class="on"></i></div>
  </div>
</footer>

<div class="bottom-bar">
  <p>Copyright 2005-2014 &nbsp;www.quelbrant-example.biz All rights reserved.</p>
  <div class="share"><i></i><span>3,450</span></div>
</div>

</body>
</html>
```